Webdesign für Honigmanufaktur
Zielgruppe
Imkerei, Verkauf von Honig und Honigerzeugnissen, so wie Bienenwachskerzen.
Zielgruppe sind vermutlich Frauen im mittleren bis gehobenen Alter.
Aufgabenstellung
Es gibt ein Firmenlogo.
Ich bevorzuge als Grundfarbe weiß, lasse mich aber von guten Einfällen gerne überraschen.
Die Website www.kelvaroni.at finde ich sehr ansprechend.
Nur ohne Musik.
Ohne Deutsch/Englisch Auswahl.
Es soll danach Word press verwendet werden.

```html
<!DOCTYPE html>
<html lang="de">
<head>
<meta charset="utf-8">
<title>Honighof Lautertal – Startseite</title>
<link rel="stylesheet" href="https://fonts.googleapis.com/css2?family=Raleway:wght@300;400;600;700;800&display=swap">
<style>
  :root {
    --brown: #4f2a0d;
    --honey: #f39a26;
    --text-grey: #8c8c8c;
    --footer-grey: #9a9a9a;
    --sand: #f6f4ef;
    --white: #ffffff;
  }
  * { box-sizing: border-box; margin: 0; padding: 0; }
  html, body { width: 1200px; height: 640px; overflow: hidden; background: var(--white); }
  body { position: relative; font-family: "Raleway", sans-serif; color: var(--brown); }

  .corner-band { position: absolute; left: 0; top: 0; width: 189px; height: 141px; }

  .main-nav a {
    position: absolute; top: 64px; font-size: 9.6px; font-weight: 700;
    color: var(--brown); text-decoration: none; letter-spacing: 0.1px;
  }
  .main-nav a.is-active { color: var(--honey); }
  .active-mark { position: absolute; left: 286px; top: 55px; width: 26px; height: 29px; }

  .brand {
    position: absolute; left: 500px; top: 36px; width: 200px; text-align: center;
  }
  .brand-dot {
    display: block; width: 44px; height: 44px; margin: 0 auto 10px;
    border-radius: 50%; background: var(--honey);
  }
  .brand-name {
    font-size: 15px; font-weight: 800; line-height: 17px; letter-spacing: 1.5px;
    color: var(--brown);
  }

  .hero-title {
    position: absolute; left: 77px; top: 234px;
    font-size: 22.5px; font-weight: 800; line-height: 27px; letter-spacing: -0.2px;
  }
  .hero-title .line-brown { color: var(--brown); display: block; }
  .hero-title .line-honey { color: var(--honey); display: block; }

  .hero-copy {
    position: absolute; left: 77px; top: 319px; width: 462px;
    font-size: 10.1px; font-weight: 400; line-height: 12px; color: var(--text-grey);
  }
  .hero-copy p + p { margin-top: 12px; }

  .more-link {
    position: absolute; left: 77px; top: 472px; display: flex; align-items: center;
    text-decoration: none; color: var(--brown); font-size: 11.2px; font-weight: 700;
  }
  .more-link svg { margin-left: 19px; width: 30px; height: 27px; }

  .honey-visual {
    position: absolute; left: 953px; top: 59px; width: 247px; height: 253px;
    background: radial-gradient(ellipse at 45% 40%, #e49a3d 0%, #f2b24a 35%, #fbd77f 60%, rgba(255,255,255,0) 75%);
  }
  .hex-gallery { position: absolute; left: 0; top: 0; width: 1200px; height: 640px; }

  .site-footer {
    position: absolute; left: 17px; top: 615px;
    font-size: 8px; font-weight: 400; color: var(--footer-grey);
  }
</style>
</head>
<body>

<svg class="corner-band" viewBox="0 0 189 141" aria-hidden="true">
  <polygon points="0,0 189,0 112,141 0,141" fill="var(--sand)"/>
</svg>

<nav class="main-nav">
  <svg class="active-mark" viewBox="0 0 26 29" aria-hidden="true">
    <polyline points="5,6 8,1 18,1 21,6" fill="none" stroke="var(--brown)" stroke-width="2"/>
    <polyline points="5,23 8,28 18,28 21,23" fill="none" stroke="var(--brown)" stroke-width="2"/>
  </svg>
  <a href="#" class="is-active" style="left:272px">STARTSEITE</a>
  <a href="#" style="left:367px">DER HONIG</a>
  <a href="#" style="left:459px">DAS TEAM</a>
  <a href="#" style="left:695px">BIENENWACHS</a>
  <a href="#" style="left:805px">SHOP</a>
  <a href="#" style="left:871px">KONTAKT</a>
</nav>

<div class="brand">
  <span class="brand-dot"></span>
  <div class="brand-name">HONIGHOF<br>LAUTERTAL</div>
</div>

<h1 class="hero-title">
  <span class="line-brown">HONIGHOF</span>
  <span class="line-honey">LAUTERTAL</span>
</h1>

<div class="hero-copy">
  <p>Lorem ipsum dolor sit amet, consetetur sadipscing elitr, sed diam nonumy eirmod tempor invidunt ut labore et dolore magna aliquyam erat, sed diam voluptua. At vero eos et accusam et justo duo dolores et ea rebum. Stet clita kasd gubergren, no sea takimata sanctus est Lorem ipsum dolor sit amet. Lorem ipsum dolor sit amet, consetetur sadipscing elitr, sed diam nonumy eirmod tempor invidunt ut labore et dolore magna aliquyam erat, sed diam voluptua. At vero eos et accusam et justo duo dolores et ea rebum. Stet clita kasd gubergren, no sea takimata sanctus est Lorem ipsum dolor sit amet.</p>
  <p>Lorem ipsum dolor sit amet, consetetur sadipscing elitr, sed diam nonumy eirmod tempor invidunt ut labore et dolore magna aliquyam erat, sed diam voluptua. At vero eos et accusam et justo duo dolores et ea rebum.</p>
</div>

<a href="#" class="more-link">MEHR ERFAHREN
  <svg viewBox="0 0 30 27" aria-hidden="true">
    <polygon points="8,1.5 22,1.5 28.5,13.5 22,25.5 8,25.5 1.5,13.5" fill="none" stroke="var(--honey)" stroke-width="2"/>
    <polyline points="13,9 17.5,13.5 13,18" fill="none" stroke="var(--brown)" stroke-width="2"/>
  </svg>
</a>

<div class="honey-visual" role="img" aria-label="Honiglöffel aus Holz, von dem goldener Honig in eine Pfütze tropft"></div>

<svg class="hex-gallery" viewBox="0 0 1200 640" role="img" aria-label="Biene beim Sammeln von Pollen auf einer gelben Blüte, in Sechseckwaben aufgeteilt">
  <defs>
    <linearGradient id="hexGold" x1="0" y1="0" x2="1" y2="1">
      <stop offset="0" stop-color="#d7a531"/>
      <stop offset="0.45" stop-color="#b8751f"/>
      <stop offset="0.75" stop-color="#c9861f"/>
      <stop offset="1" stop-color="#f2c845"/>
    </linearGradient>
  </defs>
  <polygon points="714,222 881,222 956,361 881,501 714,501 638,361" fill="url(#hexGold)"/>
  <polygon points="958,363 1123,363 1200,505 1200,640 958,640 883,502" fill="url(#hexGold)"/>
  <polygon points="714,502 881,502 955,640 640,640" fill="url(#hexGold)"/>
  <g fill="none" stroke="var(--white)" stroke-width="1.5">
    <polyline points="714,501 881,501 956,361"/>
    <polyline points="881,501 956,640"/>
  </g>
</svg>

<footer class="site-footer">Copyright 2018 - Honighof Lautertal - Alle Rechte vorbehalten | Impressum | Datenschutzerklärung</footer>

</body>
</html>
```